Fun, Clean Business Card For Family Focused Travel Agency

I need a business card using specific colors and fonts as in the uploaded files. Ideally, I would like a large image of the logo on the back and all the contact info on the front. Maybe the stars/dots somewhere in a flowy form.

I do want it the contact information to be clear and easy to read. I don't want it to look too busy. Maybe even a bit minimalist.

I plan or ordering the ROUNDED CORNER business cards from Cardwell Press, so please consider that in your design.

Target Market(s)

Families with children, couples, groups of friends

Contact Information for Business Card

Marla Quint, Owner
Marla@TumbleTrips.example
Cell Phone Number 555-218-4603
Office Phone Number 555-647-1925
Specializing in Glimmerland destinations, Pelican Bay Fun Park, Cruises and All-Inclusive Vacations.

Nice but not required:
www.TumbleTrips.example
Facebook, Instagram, Twitter icons with username: TumbleTrips

Font styles to use
Sans Serif

Requirements
Must have
• Please try to use the colors from the logo as much as possible. I understand lighter shades/colors may be needed for some things.
Should not have
• NO SERIF FONTS. That is really the only thing I do not want at all

```html
<!DOCTYPE html>
<html lang="en">
<head>
<meta charset="utf-8">
<title>TumbleTrips Business Card</title>
<link rel="stylesheet" href="https://fonts.googleapis.com/css2?family=Courgette&family=Nunito+Sans:wght@400;700&display=swap">
<style>
  :root {
    --stage: #2a2a2a;
    --card: #ffffff;
    --navy: #141a2e;
    --teal: #1aa98f;
    --orange: #f07a22;
    --yellow: #e8b21a;
    --green: #8bc34a;
    --blue: #2a9fd6;
    --ink: #2b2b2b;
    --rule: #8d8d8d;
    --swirl: #d6d6da;
  }
  * { box-sizing: border-box; margin: 0; padding: 0; }
  html, body { width: 1200px; height: 895px; overflow: hidden; }
  body { background: var(--stage); position: relative; font-family: "Nunito Sans", sans-serif; }

  .card {
    position: absolute; left: 290px; width: 620px; height: 354px;
    background: var(--card); border-radius: 26px; overflow: hidden;
  }
  .card--back { top: 62px; }
  .card--front { top: 478px; }

  .brand {
    position: absolute; inset: 0; display: flex; align-items: center; justify-content: center; gap: 18px;
  }
  .brand__dot { width: 46px; height: 46px; border-radius: 50%; background: var(--teal); }
  .brand__name { font-size: 62px; font-weight: 700; color: var(--navy); letter-spacing: .5px; }

  .swirl { position: absolute; inset: 0; width: 100%; height: 100%; }

  .holder { position: absolute; top: 46px; left: 0; right: 0; text-align: center; }
  .holder__name { font-family: "Courgette", cursive; font-size: 44px; font-weight: 400; color: var(--teal); line-height: 1; }
  .holder__role { font-size: 15px; color: var(--ink); margin-top: 4px; }

  .specialties {
    position: absolute; top: 150px; right: 328px; text-align: right; font-size: 15px; line-height: 1.4; color: var(--ink);
  }
  .specialties__title { color: var(--orange); font-weight: 700; font-size: 15px; letter-spacing: .5px; }

  .divider { position: absolute; left: 310px; top: 148px; width: 1.5px; height: 100px; background: var(--rule); }

  .contacts { position: absolute; top: 146px; left: 328px; list-style: none; font-size: 15px; line-height: 1.7; color: var(--ink); }
  .contacts li { display: flex; align-items: center; gap: 10px; }
  .contacts svg { width: 15px; height: 15px; flex: none; }

  .social { position: absolute; bottom: 54px; left: 0; right: 0; display: flex; justify-content: center; align-items: center; gap: 10px; font-size: 16px; color: var(--ink); }
  .social__dot { width: 16px; height: 16px; border-radius: 50%; background: var(--blue); }
</style>
</head>
<body>

<section class="card card--back">
  <div class="brand">
    <span class="brand__dot"></span>
    <span class="brand__name">TumbleTrips</span>
  </div>
</section>

<section class="card card--front">
  <svg class="swirl" viewBox="0 0 620 354" role="img" aria-label="Soft grey brushed oval swirl framing the card">
    <ellipse cx="310" cy="185" rx="300" ry="160" fill="none" stroke="var(--swirl)" stroke-width="22" opacity=".8"/>
  </svg>

  <header class="holder">
    <h1 class="holder__name">Marla Quint</h1>
    <p class="holder__role">Owner</p>
  </header>

  <div class="specialties">
    <p class="specialties__title">SPECIALIZING IN</p>
    <p>Pelican Bay Fun Park</p>
    <p>Glimmerland destinations</p>
    <p>Cruises and All-Inclusive Vacations</p>
  </div>

  <div class="divider"></div>

  <ul class="contacts">
    <li><svg viewBox="0 0 16 16"><rect x="4" y="1" width="8" height="14" rx="1.5" fill="none" stroke="var(--yellow)" stroke-width="1.6"/><circle cx="8" cy="12.5" r=".9" fill="var(--yellow)"/></svg>555-218-4603</li>
    <li><svg viewBox="0 0 16 16"><path d="M2 6c0-2 2.5-3 6-3s6 1 6 3l-2.5 1-1-2h-5l-1 2z" fill="var(--green)"/><rect x="3.5" y="8" width="9" height="6" rx="1" fill="var(--green)"/></svg>555-647-1925</li>
    <li><svg viewBox="0 0 16 16"><rect x="1.5" y="3.5" width="13" height="9" rx="1" fill="var(--blue)"/><path d="M1.5 4l6.5 5 6.5-5" fill="none" stroke="#fff" stroke-width="1.2"/></svg>Marla@TumbleTrips.example</li>
    <li><svg viewBox="0 0 16 16"><circle cx="8" cy="8" r="6.5" fill="none" stroke="var(--teal)" stroke-width="1.6"/><path d="M1.5 8h13M8 1.5c-3 3.5-3 9.5 0 13M8 1.5c3 3.5 3 9.5 0 13" fill="none" stroke="var(--teal)" stroke-width="1.1"/></svg>www.TumbleTrips.example</li>
  </ul>

  <div class="social">
    <span class="social__dot"></span>
    <span>TumbleTrips</span>
  </div>
</section>

</body>
</html>
```